Structural Engineering Business Card

Brookvane Drafting does residential house plans for clients in Central Florida. Would like simple but elegant business card that is appropriate for a house plan engineering company. Prefer black business card with black/white them but open to other shades of blue. I uploaded a sample card that I came across that looked good but please come up with your own creative designs.

Contact Information for Business Card

Name, Title, Phone, Email, Address, website

```html
<!DOCTYPE html>
<html lang="en">
<head>
<meta charset="utf-8">
<title>Brookvane Drafting – Business Card</title>
<link rel="stylesheet" href="https://fonts.googleapis.com/css2?family=Poppins:wght@400;600;700&display=swap">
<style>
  :root {
    --canvas: #e4e4e6;
    --card-light: #f5f1f1;
    --card-light-2: #ebe5e5;
    --card-dark: #000000;
    --ink: #111111;
    --paper: #ffffff;
  }
  * { margin: 0; padding: 0; box-sizing: border-box; }
  html, body {
    width: 1200px;
    height: 900px;
    overflow: hidden;
    background: var(--canvas);
    font-family: "Poppins", sans-serif;
  }
  .business-card {
    position: absolute;
    left: 100px;
    top: 140px;
    width: 1000px;
    height: 620px;
    background: linear-gradient(160deg, var(--card-light), var(--card-light-2));
    box-shadow: 0 18px 40px rgba(0, 0, 0, 0.18);
    overflow: hidden;
  }
  .card-shapes {
    position: absolute;
    inset: 0;
    width: 100%;
    height: 100%;
  }
  .brand-name {
    position: absolute;
    left: 58px;
    top: 150px;
    font-weight: 700;
    font-size: 37px;
    letter-spacing: -0.3px;
    color: var(--ink);
    white-space: nowrap;
  }
  .contact-block {
    position: absolute;
    left: 545px;
    top: 118px;
    color: var(--paper);
  }
  .person-name {
    font-weight: 600;
    font-size: 38px;
    line-height: 1;
    letter-spacing: 0.5px;
  }
  .person-title {
    font-size: 27px;
    line-height: 1.2;
    margin-top: 4px;
  }
  .address {
    font-style: normal;
    font-size: 27px;
    line-height: 36px;
    margin-top: 46px;
  }
  .contact-list {
    list-style: none;
    margin-top: 48px;
    font-size: 27px;
    line-height: 36.5px;
  }
  .contact-list li {
    display: flex;
    align-items: center;
    gap: 10px;
  }
  .contact-icon {
    width: 28px;
    height: 28px;
    flex: none;
  }
</style>
</head>
<body>
  <div class="business-card">
    <svg class="card-shapes" viewBox="0 0 1000 620" preserveAspectRatio="none" aria-hidden="true">
      <path class="curve-edge" fill="#ffffff"
            d="M438 0 C497 60 497 170 466 262 C420 385 392 500 450 620 L1000 620 L1000 0 Z"/>
      <path class="dark-panel" fill="#000000"
            d="M481 0 C527 62 520 170 490 262 C446 385 405 500 458 620 L1000 620 L1000 0 Z"/>
    </svg>

    <div class="brand-name">Brookvane Drafting</div>

    <div class="contact-block">
      <div class="person-name">JONATHAN SMITH</div>
      <div class="person-title">Managing Director</div>
      <address class="address">
        421, Address line<br>
        goes here<br>
        45452,Country Name
      </address>
      <ul class="contact-list">
        <li>
          <svg class="contact-icon" viewBox="0 0 24 24" fill="none" stroke="#fff" stroke-width="2" stroke-linecap="round" stroke-linejoin="round" aria-hidden="true">
            <path d="M5 3h4l2 5-2.5 1.5a11 11 0 0 0 6 6L16 13l5 2v4a2 2 0 0 1-2 2A17 17 0 0 1 3 5a2 2 0 0 1 2-2"/>
            <path d="M15 3a6 6 0 0 1 6 6M15 7a2 2 0 0 1 2 2"/>
          </svg>
          <span>044-123 456 789</span>
        </li>
        <li>
          <svg class="contact-icon" viewBox="0 0 24 24" aria-hidden="true">
            <rect x="2" y="6" width="20" height="13" fill="#fff"/>
            <path d="M2 6l10 7 10-7M2 19l8-6M22 19l-8-6" fill="none" stroke="#000" stroke-width="1.5"/>
          </svg>
          <span>info@webname.com</span>
        </li>
        <li>
          <svg class="contact-icon" viewBox="0 0 24 24" fill="none" stroke="#fff" stroke-width="1.8" aria-hidden="true">
            <circle cx="12" cy="12" r="9"/>
            <ellipse cx="12" cy="12" rx="4" ry="9"/>
            <path d="M3 12h18M5 7h14M5 17h14"/>
          </svg>
          <span>www.websitename.com</span>
        </li>
      </ul>
    </div>
  </div>
</body>
</html>
```